verdant terraces simple classy business card design

my name is colin barrow and I run a gardening business aimed at high class verdant terraces. the business name is verdant terraces and our logo was designed on pixel harbour .My clientel are anything from residential homes to businesses. I take pride in my work and know that I offer a service like no other in my area.
The business card will be used to represent my business and I want it to be not only rememberable, but simplistic and modern. Eye catching too. Of course I would like it relatable to gardening and appealing to the correct clientel - those being garden enthusiasts, prestigious homes and businesses that are after top of the line gardening services like no other on the market.
I am not a typical lawn mowing business so I don't want a typical card design that represents that. The gardens I work with are generally million dollar properties with owners who are very garden proud looking for upkeep and guidance from me along with sometimes whole new garden designs. I want the business cards to show to my clients that I take pride, as they do, in their garden. And I want them to know from my card that I am a professional, qualified horticulturist offering them a top of the line service for life. I want them to refer my business on. I want them to look at my business card and see class and professionalism in a modern unique bold way.
The card should be simple with the possibility of the logo on the front being embossed/debossed and my details on the back the card should have a organic garden feel it's very important to me that it is absolutely perfect
I am also very open to ideas and suggestions so look forward to seeing the designs. the business logo has been supplied with this project and I want the card to be double sided

Contact info is
Colin Barrow - Managing Director / Horticulturist
Phone : 0481 526 704
Email: colinbarrow@verdantterraces.example.au

Target Market(s)

high class gardens residential and commercial

Industry/Entity Type

Gardener

Contact Information for Business Card

Contact info is
Phone : 0481 526 704

PLEASE MAKE CARD DOUBLE SIDED

Requirements
Must have
• organic simple classy modern feel
• must flow with the current logo that has been supplied with this project
• Double sided
• Must explain in a simple way that I deal with high end gardens and I'm a qualified horticulturist
Nice to have
• embossed debossed logo
Should not have
• shouldn't be to busy or cheap looking

```html
<!DOCTYPE html>
<html lang="en">
<head>
<meta charset="utf-8">
<title>Verdant Terraces – Business Card</title>
<link rel="stylesheet" href="https://fonts.googleapis.com/css2?family=Arimo:wght@400;500&display=swap">
<style>
  :root {
    --backdrop: #9b9d9c;
    --paper: #f1f2f1;
    --leaf: #4f8a47;
    --slate: #7a7b7d;
    --ink: #2b2b2b;
    --ink-soft: #4a4a4a;
    --on-leaf: #e9efe6;
  }
  * { margin: 0; padding: 0; box-sizing: border-box; }
  html, body {
    width: 1105px; height: 1200px; overflow: hidden;
    background: var(--backdrop);
  }
  .card {
    position: absolute;
    left: 182px;
    width: 748px;
    height: 426px;
    overflow: hidden;
  }
  .card--front { top: 120px; background: var(--paper); }
  .card--back { top: 635px; background: var(--leaf); }

  .brand-name {
    position: absolute;
    display: flex;
    align-items: center;
    gap: 14px;
    font-family: "Arimo", sans-serif;
    font-weight: 500;
    line-height: 1;
    white-space: nowrap;
  }
  .brand-name__dot { width: 28px; height: 28px; border-radius: 50%; flex: none; }
  .brand-name__text { font-size: 34px; }

  .card--front .brand-name { left: 28px; top: 150px; color: var(--leaf); }
  .card--front .brand-name__dot { background: var(--leaf); }

  .card--back .brand-name {
    left: 50%; top: 50%; transform: translate(-50%, -50%);
    color: var(--on-leaf);
  }
  .card--back .brand-name__text { font-size: 42px; }
  .card--back .brand-name__dot { background: var(--on-leaf); width: 34px; height: 34px; }

  .contact { position: absolute; left: 28px; top: 228px; font-family: "Arimo", sans-serif; }
  .contact__name { font-size: 25px; font-weight: 500; color: var(--leaf); }
  .contact__role { font-size: 20px; color: var(--ink); margin-top: 8px; }
  .contact__lines { margin-top: 20px; font-size: 18px; color: var(--ink-soft); }
  .contact__lines p + p { margin-top: 10px; }
  .contact__label { color: var(--leaf); font-weight: 500; }

  .bands { position: absolute; left: 0; top: 0; }
  .website {
    position: absolute; right: 22px; top: 388px;
    font-family: "Arimo", sans-serif; font-size: 19px; letter-spacing: 1.2px;
    color: #fff;
  }
</style>
</head>
<body>
  <section class="card card--front" aria-label="Business card front">
    <div class="brand-name">
      <span class="brand-name__dot" aria-hidden="true"></span>
      <span class="brand-name__text">Verdant Terraces</span>
    </div>

    <div class="contact">
      <h1 class="contact__name">Colin Barrow</h1>
      <p class="contact__role">Managing Director / Horticulturist</p>
      <div class="contact__lines">
        <p><span class="contact__label">P</span> : 0481 526 704</p>
        <p><span class="contact__label">E</span> : colinbarrow@verdantterraces.example.au</p>
      </div>
    </div>

    <svg class="bands" width="748" height="426" viewBox="0 0 748 426" aria-hidden="true">
      <polygon points="0,389 398,389 382,410 0,410" fill="var(--slate)"/>
      <polygon points="414,373 748,373 748,426 0,426 0,416 393,416" fill="var(--leaf)"/>
    </svg>
    <p class="website">verdantterraces.example.au</p>
  </section>

  <section class="card card--back" aria-label="Business card back">
    <div class="brand-name">
      <span class="brand-name__dot" aria-hidden="true"></span>
      <span class="brand-name__text">Verdant Terraces</span>
    </div>
  </section>
</body>
</html>
```